Pepper & Palm Business Card FUN & EXCITING

Here is the Information for the Card:
Jaswinder Bains (Ravi)
E: RaviBains@postlark.com
C: (480) 555-0147
www.PepperPalmLV.com

We don't want traditional Indian cliche, We a playful bold and fun business card.

Files: https://files.cloudvessel.net/share/folders/7TqRmXpZ2vKa9LwBn4YcHd3JsEf6UoGi?usp=share_link

https://files.cloudvessel.net/share/folders/4MzXaQ8rTw2YbNcVk6PsLe5GhJdR3FoU?usp=share_link

Target Market(s)

Las Vegas Local Restaurant

Industry/Entity Type

Indian Restaurant

Contact Information for Business Card

Name, Email, Cell Phone, Company Logo

```html
<!DOCTYPE html>
<html lang="en">
<head>
<meta charset="UTF-8">
<title>Pepper &amp; Palm — Business Card</title>
<link href="https://fonts.googleapis.com/css2?family=Lato:wght@400;900&family=Lobster+Two:ital,wght@1,700&display=swap" rel="stylesheet">
<style>
  :root {
    --stage: #959595;
    --paper: #ffffff;
    --brand-pink: #d81b5a;
    --brand-teal: #17a98e;
    --ink: #27223d;
    --leather-light: #d9a05a;
    --leather-mid: #c48a43;
    --leather-dark: #9c6a2c;
  }
  * { box-sizing: border-box; margin: 0; padding: 0; }
  html, body {
    width: 1200px; height: 1200px; overflow: hidden;
    background: var(--stage);
  }
  .card {
    position: absolute; left: 226px; width: 746px; height: 435px;
  }
  .card--front { top: 91px; background: var(--paper); }
  .card--back {
    top: 601px;
    background:
      radial-gradient(ellipse at 30% 40%, var(--leather-light), transparent 60%),
      radial-gradient(ellipse at 75% 70%, var(--leather-light), transparent 55%),
      linear-gradient(135deg, var(--leather-mid), var(--leather-dark));
  }
  .brand-name {
    position: absolute; top: 44px; left: 0; width: 100%;
    text-align: center;
    font-family: "Lato", sans-serif; font-weight: 900;
    font-size: 38px; line-height: 1; letter-spacing: 1px;
    color: var(--brand-pink);
  }
  .person-name, .person-nickname {
    position: absolute; left: 0; width: 100%; text-align: center;
    font-family: "Lobster Two", cursive; font-style: italic; font-weight: 700;
    color: var(--brand-pink); line-height: 1;
  }
  .person-name { top: 130px; font-size: 54px; }
  .person-nickname { top: 198px; font-size: 40px; }
  .rule {
    position: absolute; top: 269px; left: 75px; width: 594px; height: 2px;
    background: var(--brand-teal);
  }
  .contact-row {
    position: absolute; top: 296px; left: 50px; width: 646px; height: 88px;
    display: flex;
  }
  .contact-item {
    display: flex; flex-direction: column; align-items: center;
    padding-top: 7px;
    font-family: "Lato", sans-serif; font-weight: 400; font-size: 20px;
    color: var(--ink); white-space: nowrap;
  }
  .contact-item--phone { width: 197px; }
  .contact-item--email { width: 245px; border-left: 2px solid var(--brand-teal); border-right: 2px solid var(--brand-teal); }
  .contact-item--web { width: 204px; }
  .contact-icon { width: 40px; height: 40px; margin-bottom: 10px; }
</style>
</head>
<body>
  <section class="card card--front">
    <div class="brand-name">Pepper &amp; Palm</div>
    <h1 class="person-name">Jaswinder Bains</h1>
    <p class="person-nickname">(Ravi)</p>
    <div class="rule"></div>
    <div class="contact-row">
      <div class="contact-item contact-item--phone">
        <svg class="contact-icon" viewBox="0 0 40 40" aria-hidden="true">
          <circle cx="20" cy="20" r="20" fill="var(--brand-teal)"/>
          <rect x="14" y="9" width="12" height="22" rx="2" fill="none" stroke="#fff" stroke-width="2"/>
          <circle cx="20" cy="27.5" r="1.3" fill="#fff"/>
        </svg>
        <span>(480) 555-0147</span>
      </div>
      <div class="contact-item contact-item--email">
        <svg class="contact-icon" viewBox="0 0 40 40" aria-hidden="true">
          <circle cx="20" cy="20" r="20" fill="var(--brand-teal)"/>
          <rect x="10" y="13" width="20" height="14" fill="none" stroke="#fff" stroke-width="2"/>
          <path d="M10 13 L20 21 L30 13" fill="none" stroke="#fff" stroke-width="2"/>
        </svg>
        <span>ravibains@postlark.com</span>
      </div>
      <div class="contact-item contact-item--web">
        <svg class="contact-icon" viewBox="0 0 40 40" aria-hidden="true">
          <circle cx="20" cy="20" r="20" fill="var(--brand-teal)"/>
          <g fill="none" stroke="#fff" stroke-width="1.6">
            <circle cx="20" cy="20" r="10"/>
            <ellipse cx="20" cy="20" rx="4.5" ry="10"/>
            <line x1="10" y1="20" x2="30" y2="20"/>
            <line x1="12" y1="15" x2="28" y2="15"/>
            <line x1="12" y1="25" x2="28" y2="25"/>
          </g>
        </svg>
        <span>pepperpalmlv.com</span>
      </div>
    </div>
  </section>

  <section class="card card--back" role="img" aria-label="Photo of tan button-tufted leather upholstery"></section>
</body>
</html>
```